Business Card Design

- one on one personal training
- group personal training
- indoor or outdoor training available
- fitness and health assessments
- personalised fitness programs
- flexible hours for training

I am a Personal Trainer in Perth Australia. I am looking to expand my word of mouth client base.

I would like to see something that uses the colours blue, green and/or yellow.

The final design should reflect the way that I train clients, fun, motivating and perhaps a little quirky?
Updates

update with a logo with the letters MVF thank you

Hi all, Have had some great designs so far. Have decided to go double sided, perhaps to use the back to list my services. Thank you

Please check update brief. Thank you.

Target Market(s)

Professionals, ages 30 to 60

Industry/Entity Type

Training

Contact Information for Business Card

Marla Prentiss
Personal Trainer

0412 807 254
marlafitcoach@quellmail.example
http://www.marlafitcoach.example

Requirements
Must have
• A logo with the letter MVF
Nice to have
• a logo to represent either; fitness, health, change, overall well-being.
Should not have
• Please no weights or lotus flowers!!

```html
<!DOCTYPE html>
<html lang="en">
<head>
<meta charset="utf-8">
<title>Marla Prentiss Personal Training – Business Card</title>
<link rel="stylesheet" href="https://fonts.googleapis.com/css2?family=Source+Sans+3:wght@400;700;900&display=swap">
<style>
  :root {
    --cyan: #00f5ff;
    --black: #000000;
    --white: #ffffff;
    --texture-grey: #5b5b5b;
    --page: #ffffff;
    --shadow: rgba(0, 0, 0, 0.28);
  }
  * { margin: 0; padding: 0; box-sizing: border-box; }
  html, body {
    width: 1000px;
    height: 1200px;
    overflow: hidden;
    background: var(--page);
    font-family: "Source Sans 3", sans-serif;
  }
  .card {
    position: absolute;
    box-shadow: 8px 12px 14px var(--shadow);
    overflow: hidden;
  }

  /* Front */
  .card-front {
    left: 184px;
    top: 177px;
    width: 603px;
    height: 366px;
  }
  .front-texture {
    position: absolute;
    inset: 0;
    background: radial-gradient(circle at 30% 40%, #6a6a6a, var(--texture-grey) 70%);
  }
  .front-panel {
    position: absolute;
    inset: 0;
  }
  .brand-name {
    position: absolute;
    left: 24px;
    top: 22px;
    font-weight: 900;
    font-size: 40px;
    line-height: 1.05;
    color: var(--black);
  }
  .brand-dot {
    position: absolute;
    left: 62px;
    top: 172px;
    width: 176px;
    height: 176px;
    border-radius: 50%;
    background: var(--cyan);
  }
  .trainer-name {
    position: absolute;
    left: 335px;
    top: 34px;
    font-weight: 700;
    font-size: 24px;
    line-height: 1.1;
    color: var(--cyan);
  }
  .contact-line {
    position: absolute;
    left: 307px;
    display: flex;
    align-items: center;
    gap: 8px;
    color: var(--white);
    font-size: 16px;
    line-height: 20px;
  }
  .contact-line svg { width: 20px; height: 20px; flex: none; }
  .contact-phone { top: 68px; }
  .contact-email { top: 224px; }
  .contact-web { top: 256px; }

  /* Back */
  .card-back {
    left: 184px;
    top: 623px;
    width: 603px;
    height: 363px;
    background: var(--cyan);
  }
  .services {
    position: absolute;
    left: 295px;
    top: 178px;
    list-style: none;
    color: var(--white);
    font-size: 15px;
    line-height: 29.5px;
  }
  .services strong { font-weight: 700; }
</style>
</head>
<body>

<section class="card card-front" aria-label="Business card front">
  <div class="front-texture" role="img" aria-label="Grey abstract scribble texture background"></div>

  <svg class="front-panel" viewBox="0 0 603 366" width="603" height="366" aria-hidden="true">
    <polygon fill="var(--black)"
      points="288,0 603,0 603,130 434,130 434,189 603,189 603,288 434,288 434,366 288,366"/>
  </svg>

  <div class="brand-name">MVF<br>Personal<br>Training</div>
  <div class="brand-dot" aria-hidden="true"></div>

  <h1 class="trainer-name">Marla Prentiss</h1>

  <div class="contact-line contact-phone">
    <svg viewBox="0 0 20 20" aria-hidden="true">
      <rect x="5" y="2" width="10" height="16" rx="2" fill="var(--white)"/>
      <rect x="7" y="4" width="6" height="7" fill="var(--black)"/>
      <circle cx="10" cy="14.5" r="1.3" fill="var(--black)"/>
    </svg>
    <span>0412 807 254</span>
  </div>

  <div class="contact-line contact-email">
    <svg viewBox="0 0 20 20" aria-hidden="true">
      <rect x="2" y="4.5" width="16" height="11" fill="none" stroke="var(--white)" stroke-width="1.8"/>
      <polyline points="2,4.5 10,11 18,4.5" fill="none" stroke="var(--white)" stroke-width="1.8"/>
    </svg>
    <span>marlafitcoach@quellmail.example</span>
  </div>

  <div class="contact-line contact-web">
    <svg viewBox="0 0 20 20" aria-hidden="true">
      <circle cx="10" cy="10" r="8" fill="none" stroke="var(--white)" stroke-width="1.8"/>
      <ellipse cx="10" cy="10" rx="3.5" ry="8" fill="none" stroke="var(--white)" stroke-width="1.4"/>
      <line x1="2" y1="10" x2="18" y2="10" stroke="var(--white)" stroke-width="1.4"/>
    </svg>
    <span>www.marlafitcoach.example</span>
  </div>
</section>

<section class="card card-back" aria-label="Business card back">
  <ul class="services">
    <li>one on one <strong>personal training</strong></li>
    <li>group <strong>personal training</strong></li>
    <li>indoor or outdoor <strong>training</strong> available</li>
    <li>fitness and health <strong>assessments</strong></li>
    <li>personalised <strong>fitness programs</strong></li>
  </ul>
</section>

</body>
</html>
```